I need a business card design for a new dance business. I offer classical Indian dance tuition and also professional performances. I want to offer the community a variety of Indian dance experiences which include: group class and private tuition, school and preschool educational courses and workshops. dance theatre performances, community function workshops and performances, Kids Bollywood parties, wedding & conference performances, mouth percussion classes, Indian mythology/ dance costume and make up workshops.
The final design should communicate a feeling and impression of the vibrance and energy of Indian dance.
Updates
Hi Everyone,
Project Deadline Extended
Reason: I would like to refine a few changes to the details of this lovely design and we have run out of time!
Project Deadline Extended
Reason: Still waiting to hear back form designer re two possible changes to the card design. Tomorrow is the deadline and I have sent several messages but with no response. I need to see this through before selecting this lovely design.
Thank you.
Tara
Industry/Entity Type
Preschool
Requirements
Must have
- The front of the business card should have the photo of me (my face and torso), surrounded entirely by a border of bright magenta (to match the magenta of my lipstick - it is the same as the magenta on my skirt in the second photo). Within the top border I want (perhaps yellow-gold) writing to say "Tara Holloway - Artistic Director" and within the bottom border it should read "Saffron Lantern Indian Dance." If you turn the card on its side the left border should have my telephone number: 0417 862 493 and the right-hand border should read: saffronlanternindiandance@quillmail.example
The reverse of the card should be the orange of the dance costume
and I'd like the picture of my feet and legs to be on the right side of the back of the card as a side border. Centre-aligned on the orange background it should read (perhaps in dark magenta):
Indian dance classes + private tuition
School + preschool educational courses and workshops
Dance theatre performances
Community function workshops and performances
Children's Bollywood parties
Wedding + conference performances
Mouth percussion classes
Indian mythology and dance demonstration workshops
Dance costume and make-up workshops
Nice to have
- A lovely artistic but easy-to-read font would be nice.

```html
<!DOCTYPE html>
<html lang="en">
<head>
<meta charset="utf-8">
<title>Saffron Lantern Indian Dance – Business Card</title>
<link href="https://fonts.googleapis.com/css2?family=Cinzel:wght@400;600&display=swap" rel="stylesheet">
<style>
  :root {
    --stage: #d6d6d6;
    --card-light: #ffffff;
    --card-shade: #dcdcdc;
    --gold-deep: #c49a1e;
    --gold-mid: #dcb43a;
    --gold-light: #e9cc6a;
    --ink: #1e140c;
    --white: #ffffff;
    --photo-saffron: #e39a2a;
    --photo-maroon: #7a1f35;
    --photo-magenta: #a3246a;
    --photo-skin: #e8c3a8;
  }
  * { margin: 0; padding: 0; box-sizing: border-box; }
  html, body {
    width: 1200px; height: 900px; overflow: hidden;
    background: var(--stage);
    font-family: "Cinzel", "Times New Roman", serif;
  }
  .canvas { position: relative; width: 1200px; height: 900px; }

  .card {
    position: absolute; width: 720px; height: 476px; overflow: hidden;
    background: linear-gradient(180deg, var(--card-light) 0%, var(--card-light) 45%, var(--card-shade) 100%);
  }
  .card--front { left: 70px; top: 40px; z-index: 2; }
  .card--back { left: 410px; top: 384px; z-index: 1; }

  .gold-band {
    position: absolute; left: 0; right: 0;
    background: linear-gradient(90deg, var(--gold-deep) 0%, var(--gold-mid) 55%, var(--gold-light) 100%);
  }
  .card--front .gold-band { top: 26px; height: 142px; }
  .card--back .gold-band { top: 134px; height: 166px; }

  .photo { position: absolute; }
  .photo--portrait {
    left: 0; top: 0; width: 456px; height: 476px;
    background:
      radial-gradient(ellipse 90px 110px at 200px 150px, var(--photo-skin) 0%, rgba(232,195,168,0) 100%),
      radial-gradient(ellipse 220px 170px at 200px 420px, var(--photo-maroon) 0%, rgba(122,31,53,0) 100%),
      linear-gradient(90deg, rgba(227,154,42,0.9) 0%, rgba(227,154,42,0.75) 60%, rgba(227,154,42,0) 100%);
  }
  .photo--feet {
    right: 0; top: 0; width: 220px; height: 420px;
    background:
      radial-gradient(ellipse 60px 40px at 110px 290px, var(--photo-skin) 0%, rgba(232,195,168,0) 100%),
      linear-gradient(180deg, var(--photo-magenta) 0%, var(--photo-maroon) 45%, var(--photo-saffron) 80%, rgba(227,154,42,0) 100%);
  }

  .title-block {
    position: absolute; left: 310px; top: 40px; width: 400px;
    text-align: center; color: var(--white);
  }
  .title-block__name { font-size: 42px; font-weight: 400; letter-spacing: 1px; line-height: 1.2; }
  .title-block__role { font-size: 34px; font-weight: 400; letter-spacing: 1px; line-height: 1.2; }

  .contact-block {
    position: absolute; left: 310px; top: 360px; width: 400px;
    text-align: center; color: var(--ink);
  }
  .contact-block__business { font-size: 22px; font-weight: 600; line-height: 1.3; }
  .contact-block__phone { font-size: 34px; font-weight: 400; line-height: 1.2; letter-spacing: 1px; }
  .contact-block__email { font-size: 14px; font-weight: 600; line-height: 1.6; }

  .services {
    position: absolute; left: 10px; top: 145px; width: 480px;
    list-style: none; text-align: center; color: var(--ink);
    font-size: 13px; font-weight: 600; line-height: 16px;
    white-space: nowrap;
  }
</style>
</head>
<body>
<main class="canvas">
  <section class="card card--front" aria-label="Business card front">
    <div class="gold-band"></div>
    <div class="photo photo--portrait" role="img" aria-label="Photo of the dancer in a saffron and maroon costume with a floral hair ornament, posing with raised hands"></div>
    <header class="title-block">
      <h1 class="title-block__name">Tara Holloway</h1>
      <p class="title-block__role">Artistic Director</p>
    </header>
    <div class="contact-block">
      <p class="contact-block__business">Saffron Lantern Indian Dance</p>
      <p class="contact-block__phone">0417 862 493</p>
      <p class="contact-block__email">saffronlanternindiandance@quillmail.example</p>
    </div>
  </section>

  <section class="card card--back" aria-label="Business card back">
    <div class="gold-band"></div>
    <ul class="services">
      <li>Indian dance classes + private tuition</li>
      <li>School + preschool educational courses and workshops</li>
      <li>Dance theatre performances</li>
      <li>Community function workshops and performances</li>
      <li>Children's Bollywood parties</li>
      <li>Wedding + conference performances</li>
      <li>Mouth percussion classes</li>
      <li>Indian mythology and dance demonstration workshops</li>
      <li>Dance costume and make-up workshops</li>
    </ul>
    <div class="photo photo--feet" role="img" aria-label="Photo of the dancer's legs and hennaed feet in a magenta and gold costume with ankle bells"></div>
  </section>
</main>
</body>
</html>
```